Business card design needed

I run a Beautician studio (for 7 years now)
I offer
- Velmo Body Sugaring
- Ruby Glaze
- Nails
- Facials
- Manicure
- Foot Treatment
It might not be necessary to list all those treatments?
Maybe the link to the Website is sufficient?
I leave that up to you ...
(more info on www.FernAndDewByLenka.com.au)
Velmo BodySugaring is our biggest success, It replaces waxing.
I would like to incorporate the logo into the Business Card.
We had many complaints regarding our old Business Cards as the Phone Number was to small.
On the backside, we would like a "your next Appointment" section.
Looking forward to you Design, cheers ... Lenka
Industry/Entity Type
Business
Contact Information for Business Card
Fern by Dew by Lenka
14 Korrin Sqr 3942 Larnhill
www.FernAndDewByLenka.com.au
03 9481 2267

```html
<!DOCTYPE html>
<html lang="en">
<head>
<meta charset="utf-8">
<title>Fern &amp; Dew by Lenka – Business Card</title>
<link rel="stylesheet" href="https://fonts.googleapis.com/css2?family=Ubuntu:wght@400;500&family=Open+Sans:ital,wght@0,400;0,600;1,700&family=Tinos&display=swap">
<style>
  :root {
    --stage: #ebe7e2;
    --card: #ffffff;
    --ink: #333333;
    --title: #454545;
    --rule: #9a9a9a;
    --band-dark: #4a4a4a;
    --band-light: #6b6b6b;
    --accent: #f0a335;
    --faint: #f4eee6;
    --faint-circle: #fcf5ec;
  }
  * { box-sizing: border-box; margin: 0; padding: 0; }
  html, body { width: 1200px; height: 788px; overflow: hidden; }
  body {
    position: relative;
    background: var(--stage);
    font-family: "Open Sans", Arial, sans-serif;
    color: var(--ink);
  }
  .view-label {
    position: absolute;
    font-size: 20px;
    color: #222;
    transform: translateX(-50%);
  }
  .card {
    position: absolute;
    background: var(--card);
    border-radius: 18px;
    overflow: hidden;
    box-shadow: 0 2px 6px rgba(0,0,0,.18);
  }
  .card-title {
    position: absolute;
    left: 0; right: 0;
    text-align: center;
    font-family: "Ubuntu", sans-serif;
    font-weight: 400;
    color: var(--title);
    letter-spacing: 1px;
  }
  .brand-name {
    font-family: "Ubuntu", sans-serif;
    font-weight: 400;
    color: var(--title);
    white-space: nowrap;
  }
  .brand-dot {
    display: inline-block;
    border-radius: 50%;
    background: var(--accent);
  }

  /* Front */
  .front { left: 341px; top: 74px; width: 524px; height: 300px; }
  .front .card-title { top: 24px; font-size: 35px; }
  .front .brand {
    position: absolute; left: 0; right: 0; top: 104px;
    display: flex; flex-direction: column; align-items: center; gap: 12px;
  }
  .front .brand-dot { width: 52px; height: 52px; }
  .front .brand-name { font-size: 18px; }
  .contact {
    position: absolute; left: 0; right: 0;
    text-align: center; font-size: 16px;
  }
  .contact b { font-weight: 700; font-style: italic; }
  .contact-line-1 { top: 212px; }
  .contact-line-2 { top: 240px; }
  .front .band { position: absolute; left: 0; bottom: 0; width: 100%; height: 24px; }

  /* Back 1 */
  .back-one { left: 54px; top: 444px; width: 525px; height: 299px; }
  .back-one .card-title { top: 12px; font-size: 26px; z-index: 2; }
  .back-one .title-rule { position: absolute; left: 0; right: 0; top: 50px; height: 1px; background: var(--rule); }
  .back-one .faint-mark {
    position: absolute; left: 165px; top: 90px; width: 200px; height: 200px;
    border-radius: 50%; background: var(--faint-circle);
  }
  .back-one .faint-name {
    position: absolute; left: 130px; top: 190px;
    font-family: "Ubuntu", sans-serif; font-size: 58px; letter-spacing: 8px;
    color: var(--faint);
  }
  .section-head {
    position: absolute; font-weight: 700; font-style: italic; font-size: 18px;
  }
  .offer-head { left: 29px; top: 68px; }
  .offer-list {
    position: absolute; left: 29px; top: 96px; list-style: none;
    font-family: "Tinos", serif; font-size: 15px; line-height: 20px;
  }
  .offer-list li::before { content: "\25AA"; margin-right: 6px; font-size: 11px; }
  .column-divider {
    position: absolute; left: 206px; top: 60px; width: 2px; height: 155px; background: #777;
  }
  .appt-head { left: 244px; top: 68px; }
  .appt-field {
    position: absolute; left: 244px; font-size: 16px; display: flex; align-items: flex-end;
  }
  .appt-field .blank { border-bottom: 1px solid var(--ink); height: 18px; margin-left: 2px; }
  .field-name { top: 110px; }
  .field-date { top: 150px; }
  .field-time { top: 190px; }
  .hours-compact {
    position: absolute; left: 0; right: 0; top: 238px; text-align: center;
  }
  .hours-compact h3 { font-size: 14px; font-weight: 700; font-style: italic; }
  .hours-compact p { font-size: 12.5px; word-spacing: 1px; }
  .hours-compact span { margin-left: 42px; }

  /* Back 2 */
  .back-two { left: 621px; top: 444px; width: 525px; height: 299px; }
  .back-two .hours-head {
    position: absolute; left: 33px; top: 27px;
    font-weight: 700; font-style: italic; font-size: 20px; letter-spacing: 1.2px;
  }
  .back-two .hours-lines {
    position: absolute; left: 30px; top: 60px; font-size: 17.5px; line-height: 24px;
  }
  .back-two .brand {
    position: absolute; left: 362px; top: 22px; width: 135px;
    display: flex; flex-direction: column; align-items: center; gap: 8px;
  }
  .back-two .brand-dot { width: 48px; height: 48px; }
  .back-two .brand-name { font-size: 13px; }
  .back-two .divider { position: absolute; left: 30px; top: 116px; width: 466px; height: 1px; background: #c8c8c8; }
  .appt-line { position: absolute; left: 46px; top: 142px; font-size: 18px; display: flex; align-items: flex-end; }
  .appt-line .blank { width: 260px; border-bottom: 1px solid var(--ink); margin-right: 4px; height: 20px; }
  .date-line { position: absolute; left: 35px; top: 192px; font-size: 18px; display: flex; align-items: flex-end; gap: 6px; }
  .date-line .blank { border-bottom: 1px solid var(--ink); height: 20px; }
  .day-boxes { position: absolute; left: 60px; top: 248px; display: flex; gap: 14px; font-size: 17px; }
  .day-boxes label { display: flex; align-items: center; gap: 12px; margin-right: 6px; }
  .day-boxes .box { width: 22px; height: 22px; border: 1.5px solid var(--ink); }
</style>
</head>
<body>

<span class="view-label" style="left:600px;top:34px;">Front</span>
<span class="view-label" style="left:322px;top:403px;">Back - 1</span>
<span class="view-label" style="left:897px;top:403px;">Back - 2</span>

<section class="card front">
  <h1 class="card-title">FERN&amp;DEW BY LENKA</h1>
  <div class="brand">
    <span class="brand-dot"></span>
    <span class="brand-name">Velmo Body Sugaring</span>
  </div>
  <p class="contact contact-line-1"><b>phone</b> 03 9481 2267 &nbsp;|&nbsp; <b>add</b> 14 Korrin Sqr, 3942 Larnhill</p>
  <p class="contact contact-line-2"><b>web</b> www.FernAndDewByLenka.com.au</p>
  <svg class="band" viewBox="0 0 524 24" preserveAspectRatio="none">
    <rect width="524" height="24" fill="var(--band-light)"/>
    <polygon points="0,0 232,0 256,24 0,24" fill="var(--band-dark)"/>
  </svg>
</section>

<section class="card back-one">
  <div class="faint-mark"></div>
  <div class="faint-name">VELMO</div>
  <h2 class="card-title">FERN&amp;DEW BY LENKA</h2>
  <div class="title-rule"></div>

  <h3 class="section-head offer-head">I offer</h3>
  <ul class="offer-list">
    <li>Velmo Body Sugaring</li>
    <li>Ruby Glaze</li>
    <li>Nails</li>
    <li>Facials</li>
    <li>Manicure</li>
    <li>Foot Treatment</li>
  </ul>

  <div class="column-divider"></div>

  <h3 class="section-head appt-head">An Appointment</h3>
  <div class="appt-field field-name">Name<span class="blank" style="width:216px"></span></div>
  <div class="appt-field field-date">Date<span class="blank" style="width:224px"></span></div>
  <div class="appt-field field-time">time<span class="blank" style="width:160px"></span>&nbsp;am / pm</div>

  <div class="hours-compact">
    <h3>Hours of Operation</h3>
    <p>Mon. to Fri.&nbsp; 7.30am - 7.00pm<span>Sat. 7.30am - 12.00pm</span></p>
  </div>
</section>

<section class="card back-two">
  <h3 class="hours-head">Hours of Operation</h3>
  <p class="hours-lines">Monday to Friday -&nbsp; 7.30am - 7.00pm<br>Saturday - 7.30am - 12.00pm</p>
  <div class="brand">
    <span class="brand-dot"></span>
    <span class="brand-name">Velmo Body Sugaring</span>
  </div>
  <div class="divider"></div>

  <div class="appt-line"><span class="blank"></span>has an appointment</div>
  <div class="date-line">
    Date :<span class="blank" style="width:38px"></span>/<span class="blank" style="width:42px"></span>/<span class="blank" style="width:52px"></span>&nbsp;@<span class="blank" style="width:42px"></span>&nbsp;:<span class="blank" style="width:52px"></span>am / pm
  </div>
  <div class="day-boxes">
    <label><span class="box"></span>Mon.</label>
    <label><span class="box"></span>Tue.</label>
    <label><span class="box"></span>Wed.</label>
    <label><span class="box"></span>Thu.</label>
    <label><span class="box"></span>Fri.</label>
  </div>
</section>

</body>
</html>
```